8' X 8" convention booth design

I am requesting a design for a convention booth. This design must be created in Adobe Illustrator.
I sell insurance programs to the members of associations. My prospects that will see this booth are association professionals looking to select a provider of insurance benefits for their memberships. I would like my prospects to look at my booth, see our logo, understand what we do, and then show some icons highlighting the insurance products that we have available. Please feel free to add any pictures or anything you might find to make the booth more appealing, but are not necessary. I have attached a photo of a sample of the booth construction below for your review.
The booth is 8’ X 8’ in the front and will have two 1’ side panels on each side. The dimensions of the front graphics are 87.75” W X 87.75” H. Each of the two side panel is 12 W X 87.75” H. The total width of the design is 111.75”. The graphic should be designed to include the 12’ wrap around on each side.
I have attached two of our logos below. The attached KMR logo with the words "Affinity and Association Services" is the logo for the front of the booth. The plain KMR logo is for the top of the side panels.
For side panels, please put the KMR logo (with only the KMR letters) at the top and the words "Association Insurance" underneath the KMR logo. The Association Insurance letters should be vertical.
For the front of the booth, I would like to have the KMR logo somewhere prominent in your design. I do not want it too big, but would like people to notice my company logo and description line. Also on the front of the booth, please include the following information that describes my company:
Full Portfolio of Insurance Products
Brokerage with A-Rated insurance companies
Full-Service Administrator
State-of-the-Art Technologies
Multi-Channel Marketing
The header for this section of five bullets above can be Member Insurance Program Management.
Lastly, I have attached 14 other icons that represent the insurance products I am offering. Please place them in a grid, or some other creative way, and include the word I have used to name each icon below each icon. For example, please type the word Life under the Life icon in the design. If you are looking for a header for this section, it can be Insurance Products Thank you very much for your interest.
Association Executive Directors looking to offer valuable member benefits to their association membership.
Designer to choose colors to be used in the design.

```html
<!DOCTYPE html>
<html lang="en">
<head>
<meta charset="UTF-8">
<title>KMR Association Insurance Booth</title>
<link rel="stylesheet" href="https://fonts.googleapis.com/css2?family=Poppins:wght@400;500;600;700&family=Saira+Condensed:wght@600&display=swap">
<style>
  :root {
    --green: #9aa51a;
    --charcoal: #2e2e2e;
    --white: #ffffff;
    --paper: #f4f4f4;
    --streak: #ececec;
    --stage: #d9d9d9;
    --ink: #222222;
    --muted: #555555;
    --icon-light: #e9f1fb;
    --icon-mid: #8fbbea;
  }
  * { box-sizing: border-box; margin: 0; padding: 0; }
  html, body { width: 1200px; height: 1200px; overflow: hidden; }
  body {
    background: var(--stage);
    font-family: "Poppins", sans-serif;
    position: relative;
  }
  .booth-front {
    position: absolute; left: 40px; top: 120px;
    width: 960px; height: 960px;
    background: var(--white);
    overflow: hidden;
  }
  .booth-front .backdrop { position: absolute; inset: 0; }
  .brand {
    position: absolute; left: 130px; top: 70px;
    display: flex; align-items: center; gap: 34px;
  }
  .brand-name {
    font-weight: 700; font-size: 64px; color: var(--green);
    letter-spacing: 1px; line-height: 1;
  }
  .brand-tagline {
    font-style: italic; font-weight: 500; font-size: 24px;
    letter-spacing: 3px; color: var(--muted);
  }
  .program-title {
    position: absolute; left: 62px; top: 232px;
    font-weight: 700; font-size: 40px; line-height: 1.2;
    color: var(--white);
  }
  .service-list {
    position: absolute; left: 340px; top: 250px;
    list-style: none; color: var(--white);
    font-size: 21px; font-weight: 500;
  }
  .service-list li { margin-bottom: 9px; }
  .service-list li::before {
    content: "»"; color: var(--green); font-weight: 700;
    margin-right: 10px;
  }
  .service-list li:nth-child(2) { margin-left: 12px; }
  .service-list li:nth-child(3) { margin-left: 24px; }
  .service-list li:nth-child(4) { margin-left: 36px; }
  .service-list li:nth-child(5) { margin-left: 48px; }
  .products-title {
    position: absolute; left: 0; right: 0; top: 528px;
    text-align: center; font-weight: 700; font-size: 34px;
    color: var(--ink); letter-spacing: 1px;
  }
  .product-grid {
    position: absolute; left: 50px; top: 590px; width: 860px;
    display: grid; grid-template-columns: repeat(7, 1fr);
    row-gap: 14px;
  }
  .product { display: flex; flex-direction: column; align-items: center; }
  .product-icon {
    width: 84px; height: 84px; border-radius: 50%;
    background: radial-gradient(circle at 50% 45%, var(--icon-mid) 0%, var(--icon-light) 55%, var(--white) 75%);
    box-shadow: -6px 6px 10px rgba(0,0,0,0.18);
  }
  .product-label {
    margin-top: 10px; font-weight: 600; font-size: 16px;
    color: var(--ink); text-align: center; line-height: 1.15;
  }
  .contact-bar {
    position: absolute; left: 60px; top: 868px;
    width: 840px; height: 62px;
  }
  .contact-web {
    position: absolute; right: 0; top: 0; height: 62px; width: 460px;
    background: var(--charcoal); border-radius: 31px;
    color: var(--white); font-weight: 700; font-size: 36px;
    display: flex; align-items: center; justify-content: flex-end;
    padding-right: 60px;
  }
  .contact-phone {
    position: absolute; left: 0; top: 0; height: 62px; width: 420px;
    background: var(--green); border-radius: 31px;
    color: var(--white); font-weight: 700; font-size: 32px;
    display: flex; align-items: center; padding-left: 48px;
  }
  .booth-side {
    position: absolute; left: 1020px; top: 120px;
    width: 132px; height: 960px;
    background: var(--charcoal);
    overflow: hidden;
  }
  .side-top {
    height: 210px; background: var(--white);
    display: flex; align-items: center; justify-content: center;
  }
  .side-brand { font-weight: 700; font-size: 40px; color: var(--green); }
  .side-words {
    display: flex; flex-direction: column; align-items: center;
    padding-top: 34px;
    font-family: "Saira Condensed", sans-serif; font-weight: 600;
    font-size: 30px; line-height: 33px; color: var(--white);
  }
  .side-words .gap { height: 22px; }
</style>
</head>
<body>
  <section class="booth-front">
    <svg class="backdrop" width="960" height="960" viewBox="0 0 960 960">
      <polygon points="240,0 860,0 960,120 960,960 560,960" fill="var(--paper)"/>
      <polygon points="420,480 960,560 960,960 620,960" fill="var(--streak)" opacity="0.6"/>
      <polygon points="0,205 310,210 392,480 0,458" fill="var(--green)"/>
      <polygon points="310,210 960,225 960,525 392,480" fill="var(--charcoal)"/>
    </svg>

    <header class="brand">
      <span class="brand-name">KMR</span>
      <span class="brand-tagline">AFFINITY &amp; ASSOCIATION SERVICES</span>
    </header>

    <h1 class="program-title">Member<br>Insurance<br>Program<br>Management.</h1>

    <ul class="service-list">
      <li>Brokerage with A-Rated insurance companies</li>
      <li>Full Portfolio of Insurance Products</li>
      <li>Full-Service Administrator</li>
      <li>State-of-the-Art Technologies</li>
      <li>Multi-Channel Marketing</li>
    </ul>

    <h2 class="products-title">INSURANCE PRODUCTS</h2>

    <div class="product-grid">
      <div class="product"><div class="product-icon" role="img" aria-label="Accident insurance icon"></div><span class="product-label">Accident</span></div>
      <div class="product"><div class="product-icon" role="img" aria-label="Business insurance icon"></div><span class="product-label">Business</span></div>
      <div class="product"><div class="product-icon" role="img" aria-label="Auto insurance icon"></div><span class="product-label">Auto</span></div>
      <div class="product"><div class="product-icon" role="img" aria-label="Dental insurance icon"></div><span class="product-label">Dental</span></div>
      <div class="product"><div class="product-icon" role="img" aria-label="Family health insurance icon"></div><span class="product-label">Family<br>Health</span></div>
      <div class="product"><div class="product-icon" role="img" aria-label="Financial wellness icon"></div><span class="product-label">Financial<br>Wellness</span></div>
      <div class="product"><div class="product-icon" role="img" aria-label="Long-term care insurance icon"></div><span class="product-label">Long-Term<br>Care</span></div>
      <div class="product"><div class="product-icon" role="img" aria-label="Home insurance icon"></div><span class="product-label">Home</span></div>
      <div class="product"><div class="product-icon" role="img" aria-label="Liability insurance icon"></div><span class="product-label">Liability</span></div>
      <div class="product"><div class="product-icon" role="img" aria-label="Life insurance icon"></div><span class="product-label">Life</span></div>
      <div class="product"><div class="product-icon" role="img" aria-label="Prescription card icon"></div><span class="product-label">Rx Cards</span></div>
      <div class="product"><div class="product-icon" role="img" aria-label="Travel insurance icon"></div><span class="product-label">Travel</span></div>
      <div class="product"><div class="product-icon" role="img" aria-label="Vision insurance icon"></div><span class="product-label">Vision</span></div>
      <div class="product"><div class="product-icon" role="img" aria-label="Health insurance icon"></div><span class="product-label">Health</span></div>
    </div>

    <footer class="contact-bar">
      <div class="contact-web">www.kmr.com</div>
      <div class="contact-phone">CALL: 0987 654 321</div>
    </footer>
  </section>

  <aside class="booth-side">
    <div class="side-top"><span class="side-brand">KMR</span></div>
    <div class="side-words">
      <span>A</span><span>S</span><span>S</span><span>O</span><span>C</span><span>I</span><span>A</span><span>T</span><span>I</span><span>O</span><span>N</span>
      <span class="gap"></span>
      <span>I</span><span>N</span><span>S</span><span>U</span><span>R</span><span>A</span><span>N</span><span>C</span><span>E</span>
    </div>
  </aside>
</body>
</html>
```